Business Card for Field Lotus-Eco Friendly Organic Clothing Brand

We are looking for an amazing business card for our eco friendly, organic clothing brand. We are thinking maybe a business card with a peel off sticker on the back, since our hanging clothing tag is a peel off sticker on the back. I will attach our hang tag so we can make sure we stay in line with our design. I've also attached a bag we are doing because I do like the scattered emblem look as well.

```html
<!DOCTYPE html>
<html lang="en">
<head>
<meta charset="utf-8">
<title>Field Lotus Business Card</title>
<link href="https://fonts.googleapis.com/css2?family=Source+Sans+3:wght@400;600&display=swap" rel="stylesheet">
<style>
  :root {
    --bg: #ecebe8;
    --olive-dark: #22231a;
    --card-white: #ffffff;
    --gold: #c9a23f;
    --ink: #333333;
  }
  * { margin: 0; padding: 0; box-sizing: border-box; }
  html, body { width: 1200px; height: 900px; overflow: hidden; }
  body {
    background: var(--bg);
    font-family: "Source Sans 3", sans-serif;
    position: relative;
  }
  .card {
    position: absolute;
    border-radius: 18px;
    overflow: hidden;
    box-shadow: 0 6px 18px rgba(0,0,0,0.15);
  }
  .card-front {
    left: 78px; top: 34px; width: 588px; height: 364px;
    background: var(--card-white);
  }
  .card-back {
    left: 390px; top: 506px; width: 564px; height: 350px;
    background: var(--olive-dark);
  }
  .band {
    position: absolute; left: 0; right: 0;
    display: flex; align-items: center; justify-content: center;
  }
  .card-front .band { top: 29px; height: 100px; background: var(--olive-dark); }
  .card-back .band { top: 126px; height: 96px; background: var(--card-white); }
  .brand {
    display: flex; flex-direction: column; align-items: center; gap: 4px;
  }
  .brand-name {
    display: flex; align-items: center; gap: 10px;
    color: var(--gold); font-weight: 600; font-size: 30px; letter-spacing: 2px;
  }
  .brand-mark { width: 14px; height: 14px; background: var(--gold); }
  .brand-web { color: var(--gold); font-size: 12px; }
  .contact {
    position: absolute; left: 0; right: 0; top: 174px;
    text-align: center; color: var(--ink);
  }
  .person-name { color: var(--gold); font-weight: 600; font-size: 23px; letter-spacing: 0.5px; }
  .person-title { font-size: 17px; margin-top: 2px; }
  .contact-list { list-style: none; margin-top: 18px; font-size: 17px; line-height: 24px; }
  .contact-list li { display: flex; justify-content: center; align-items: center; gap: 8px; }
  .contact-list svg { width: 12px; height: 12px; fill: var(--gold); }
  .address { font-size: 17px; margin-top: 16px; }
</style>
</head>
<body>
  <section class="card card-front">
    <div class="band">
      <div class="brand">
        <div class="brand-name"><span class="brand-mark"></span>FIELD LOTUS</div>
        <div class="brand-web">www.fieldlotus.com</div>
      </div>
    </div>
    <div class="contact">
      <p class="person-name">JOHN SMITH</p>
      <p class="person-title">Managing Direcator</p>
      <ul class="contact-list">
        <li>
          <svg viewBox="0 0 12 12"><path d="M1 3 Q6 0 11 3 L10 5 L8 4 L8 3 Q6 2.3 4 3 L4 4 L2 5 Z M3 6 H9 L10 11 H2 Z"/></svg>
          823-456-7890
        </li>
        <li>
          <svg viewBox="0 0 12 12"><path d="M1 2.5 H11 V9.5 H1 Z" /><path d="M1 2.5 L6 6.5 L11 2.5" stroke="#fff" stroke-width="1" fill="none"/></svg>
          info@youremail.com
        </li>
      </ul>
      <p class="address">1234, Address Goes HereCountry Name, 123456</p>
    </div>
  </section>

  <section class="card card-back">
    <div class="band">
      <div class="brand">
        <div class="brand-name"><span class="brand-mark"></span>FIELD LOTUS</div>
        <div class="brand-web">www.fieldlotus.com</div>
      </div>
    </div>
  </section>
</body>
</html>
```